Business card design for holistic health care clinic

We need a double-sided business card design for our holistic health care clinic that integrates our logo design and also its color scheme. My business is called Valmira. It is an integrative medicine clinic. You have already done the logo for me. Please ensure an elegant and upscale design that is not cluttered, but still has all the necessary information (please see below for details).

Target Market(s)

Wellness, fitness, rehabilitation for educated, well-traveled open-minded clients who are focused on natural, organic, balanced and preventive healthcare and lifestyle.

Industry/Entity Type

Medical

Contact Information for Business Card

Modern, clean.

Number of Pages Required

1 page

Font styles to use
Serif
Sans Serif

Colors

Designer to choose colors to be used in the design.

Requirements
Must have
• Logo on one side, all other information on the other side.
• Other information should include:
• Tobias Wrenfeld - DOE, CPT, LMT
• 4100 East Marrow Drive
• Austin, TX 78119
• 512 555 0148
• 818 555 0192
• info@ValmiraHealth.example
• t.wrenfeld@ValmiraHealth.example
Nice to have
• Darker background on front - but not totally black - shaded/dark gray.

```html
<!DOCTYPE html>
<html lang="en">
<head>
<meta charset="utf-8">
<title>Valmira — Business Card</title>
<link rel="stylesheet" href="https://fonts.googleapis.com/css2?family=Montserrat:wght@600&family=Nunito:wght@700;800&family=Source+Sans+3:wght@400&display=swap">
<style>
  :root {
    --backdrop: #ece9e6;
    --brand-blue: #0b8fcb;
    --card-dark: #1c1e20;
    --ink-white: #ffffff;
  }
  * { margin: 0; padding: 0; box-sizing: border-box; }
  html, body { width: 1200px; height: 900px; overflow: hidden; }
  body { background: var(--backdrop); position: relative; }

  .card { position: absolute; box-shadow: 0 6px 18px rgba(0,0,0,.18); }

  /* Contact side */
  .card-contact {
    left: 78px; top: 33px; width: 589px; height: 364px;
    background: var(--brand-blue); color: var(--ink-white);
    font-family: "Source Sans 3", "Myriad Pro", sans-serif;
    overflow: hidden;
  }
  .edge-band {
    position: absolute; right: 0; top: 0; width: 22px; height: 100%;
    background: var(--ink-white);
  }
  .holder {
    position: absolute; left: 28px; top: 87px;
    display: flex; align-items: baseline; gap: 9px;
  }
  .holder-name {
    font-family: "Montserrat", sans-serif; font-weight: 600;
    font-size: 17px; letter-spacing: .2px; text-transform: uppercase;
  }
  .holder-credentials { font-size: 15px; letter-spacing: .3px; }
  .address {
    position: absolute; left: 28px; top: 178px;
    font-size: 16px; line-height: 21px; font-style: normal;
  }
  .contact-list {
    position: absolute; left: 28px; top: 230px; list-style: none;
    font-size: 16px; line-height: 21.3px;
  }
  .contact-list li { display: flex; align-items: center; gap: 8px; }
  .contact-list svg { width: 12px; height: 12px; fill: var(--ink-white); flex: none; }

  /* Logo side */
  .card-logo {
    left: 388px; top: 505px; width: 567px; height: 352px;
    background: var(--card-dark);
    display: flex; flex-direction: column; align-items: center; justify-content: center;
    padding-top: 34px;
  }
  .brand-name {
    font-family: "Nunito", sans-serif; font-weight: 800;
    font-size: 52px; line-height: 1; color: var(--brand-blue);
    text-transform: uppercase; letter-spacing: 1px;
  }
  .brand-tagline {
    font-family: "Nunito", sans-serif; font-weight: 700;
    font-size: 16px; color: var(--brand-blue); margin-top: 6px;
  }
</style>
</head>
<body>

<section class="card card-contact">
  <div class="edge-band"></div>
  <div class="holder">
    <span class="holder-name">Tobias Wrenfeld</span>
    <span class="holder-credentials">DOE, CPT, LMT</span>
  </div>
  <address class="address">4100 East Marrow Drive<br>Austin, TX 78119</address>
  <ul class="contact-list">
    <li><svg viewBox="0 0 12 12"><path d="M1 4c0-2 2-3 5-3s5 1 5 3v1H8V4H4v1H1zM3 6h6l2 5H1z"/></svg>512 555 0148</li>
    <li><svg viewBox="0 0 12 12"><path d="M3 0h6v12H3zM4 1.5v8h4v-8z"/></svg>818 555 0192</li>
    <li><svg viewBox="0 0 12 12"><path d="M0 2h12v8H0zM1 3v.5l5 3.5 5-3.5V3z"/></svg>info@ValmiraHealth.example</li>
    <li><svg viewBox="0 0 12 12"><path d="M0 2h12v8H0zM1 3v.5l5 3.5 5-3.5V3z"/></svg>t.wrenfeld@ValmiraHealth.example</li>
    <li><svg viewBox="0 0 12 12"><circle cx="6" cy="6" r="5.5"/></svg>www.ValmiraHealth.example</li>
  </ul>
</section>

<section class="card card-logo">
  <div class="brand-name">Valmira</div>
  <div class="brand-tagline">Integrative Holistic Medicine</div>
</section>

</body>
</html>
```